Plotvista Caribbean

We need a vibrant, user friendly and exciting website for our land search company called "plotVista" This application will help individuals locate and or list lots for sale within the Caribbean. We will offer a small cash back incentive to buyers that purchase land from our site, and we will charge a 1%-2% success fee to our sellers once a successful transaction is made. We would like to become a match making site, matching buyers and sellers on our platform. We will also include a service directory and marketing advertisement spot for other service providers for a fee. We would like to see a webdesign incorporating Caribbean colors (blue, green and yellow) with very modern clean lines, very picturesque and easy to use.

Industry/Entity Type

Real Estate

Coding

Coded - Design and coding required

Number of Pages Required

5+ page

Font styles to use
Sans Serif

Colors
ffffff
85acd3
b768aa
dbdbdb

Requirements
Nice to have
• Scenic photos of the ocean and beautiful landscape

```html
<!DOCTYPE html>
<html lang="en">
<head>
<meta charset="utf-8">
<title>plotVista — Land Search in the Caribbean</title>
<link href="https://fonts.googleapis.com/css2?family=Raleway:wght@300;400;500;600&display=swap" rel="stylesheet">
<style>
  :root {
    --white: #ffffff;
    --blue: #85acd3;
    --magenta: #b768aa;
    --rule: #dbdbdb;
    --page-bg: #f0ebe7;
    --ink: #3a3a3a;
    --ink-soft: #555555;
  }
  * { box-sizing: border-box; margin: 0; padding: 0; }
  html, body { width: 946px; height: 1200px; overflow: hidden; }
  body {
    position: relative;
    background: var(--page-bg);
    font-family: "Raleway", sans-serif;
    color: var(--ink);
  }
  .card {
    position: absolute;
    left: 104px;
    width: 738px;
    background: var(--white);
    box-shadow: 0 1px 3px rgba(0,0,0,0.12);
  }
  .site-header { top: 0; height: 372px; }
  .content { top: 390px; height: 750px; }
  .site-footer { top: 1150px; height: 50px; }

  /* header */
  .brand {
    position: absolute; left: 16px; top: 38px;
    display: flex; align-items: center; gap: 6px;
    font-size: 20px; font-weight: 600; color: var(--ink);
  }
  .brand-dot { width: 10px; height: 10px; border-radius: 50%; background: var(--magenta); }
  .main-nav {
    position: absolute; top: 51px; left: 0; width: 100%;
    font-size: 11.5px; font-weight: 500;
  }
  .main-nav a { position: absolute; color: var(--ink); text-decoration: none; }
  .main-nav a.is-active { color: var(--magenta); }
  .search-icon { position: absolute; left: 714px; top: 52px; }

  .hero {
    position: absolute; left: 13px; top: 88px; width: 712px; height: 270px;
    background: linear-gradient(180deg, #9aa57a 0%, #c6cf9a 35%, #b8c77a 55%, #8db342 78%, #6f9e2a 100%);
  }
  .hero-box {
    position: absolute; left: 176px; top: 63px; width: 360px; height: 107px;
    background: rgba(255,255,255,0.6);
    text-align: center;
  }
  .hero-box p {
    margin-top: 14px; font-size: 16.5px; font-weight: 300; line-height: 20px; color: var(--ink);
  }
  .hero-box hr { width: 170px; margin: 9px auto 0; border: 0; border-top: 1px solid rgba(0,0,0,0.15); }
  .hero-cta {
    display: block; margin-top: 11px; font-size: 13px; font-weight: 600;
    color: var(--magenta); text-decoration: none;
  }
  .hero-dots { position: absolute; left: 328px; top: 227px; display: flex; gap: 3px; }
  .hero-dots span { width: 12px; height: 12px; border-radius: 50%; background: var(--white); border: 2px solid var(--white); }
  .hero-dots span.is-current { background: transparent; }

  /* features */
  .feature { position: absolute; left: 13px; width: 712px; }
  .feature-photo { position: absolute; left: 0; top: 0; width: 280px; height: 207px; }
  .feature-title {
    position: absolute; left: 317px; top: 14px; width: 380px;
    font-size: 24px; font-weight: 300; line-height: 27px; color: var(--magenta);
  }
  .feature-text {
    position: absolute; left: 318px; top: 85px; width: 382px;
    font-size: 9.2px; line-height: 17px; color: var(--ink-soft);
  }
  .read-more {
    position: absolute; left: 318px; font-size: 13px; font-weight: 500;
    color: var(--blue); text-decoration: none;
  }
  .divider { position: absolute; left: 13px; width: 712px; border: 0; border-top: 1px solid var(--rule); }

  /* gallery */
  .gallery-title {
    position: absolute; left: 13px; top: 552px;
    font-size: 24px; font-weight: 300; color: var(--magenta);
  }
  .gallery-arrows { position: absolute; left: 708px; top: 566px; display: flex; gap: 6px; }
  .gallery-grid { position: absolute; left: 13px; top: 590px; width: 712px; height: 132px; }
  .tile { position: absolute; }
  .tile-large { left: 0; top: 0; width: 181px; height: 132px; background: linear-gradient(180deg, #c9a46a, #7b7a45 60%, #4a4a30); }

  /* footer */
  .social { position: absolute; left: 13px; top: 17px; display: flex; gap: 7px; }
  .social span { width: 15px; height: 15px; border-radius: 2px; }
  .copyright { position: absolute; right: 17px; top: 19px; font-size: 9.5px; color: var(--ink); }
</style>
</head>
<body>

<header class="card site-header">
  <div class="brand"><span class="brand-dot"></span>plotVista</div>
  <nav class="main-nav">
    <a class="is-active" style="left:371px">Home</a>
    <a style="left:432px">About Us</a>
    <a style="left:509px">Services</a>
    <a style="left:580px">Gallery</a>
    <a style="left:646px">Contact</a>
  </nav>
  <svg class="search-icon" width="10" height="10" viewBox="0 0 10 10" aria-label="Search">
    <circle cx="4" cy="4" r="3" fill="none" stroke="#c8c8c8" stroke-width="1.4"/>
    <line x1="6.2" y1="6.2" x2="9.3" y2="9.3" stroke="#c8c8c8" stroke-width="1.6"/>
  </svg>

  <section class="hero" role="img" aria-label="Wide green valley under a cloudy sky with mountains in the distance">
    <div class="hero-box">
      <p>We help individuals locate and or list lots<br>for sale within the Caribbean</p>
      <hr>
      <a class="hero-cta" href="#">GET A QUOTE &gt;</a>
    </div>
    <div class="hero-dots"><span class="is-current"></span><span></span><span></span><span></span></div>
  </section>
</header>

<main class="card content">
  <article class="feature" style="top:13px">
    <div class="feature-photo" role="img" aria-label="Golden wheat field at sunset" style="background:linear-gradient(180deg,#d9c7a8 0%,#f0d9a0 35%,#b88a4a 55%,#7a4e22 100%)"></div>
    <h2 class="feature-title">Accusantium Doloremque Laudantium</h2>
    <p class="feature-text">Lorem ipsum dolor sit amet, consectetuer adipiscing. Praesent vestibulum molestie lacus. Aenean nonummy hendrerit mauris. Phasellus porta. Fusce suscipit varius mi. Lorem ipsum dolor sit amet, consectetuer adipiscing elit. Praesent vestibulum molestie lacus. Morbi nunc odio, gravida at, cursus nec, luctus a, lorem. Maecenas tristique orci ac sem.</p>
    <a class="read-more" href="#" style="top:180px">Read More &gt;</a>
  </article>

  <hr class="divider" style="top:251px">

  <article class="feature" style="top:278px">
    <div class="feature-photo" role="img" aria-label="Green mountain valley with trees, a fence and a stony stream bank" style="background:linear-gradient(180deg,#c5d3e0 0%,#6f8a6a 25%,#5f9a30 55%,#7fb83a 80%,#b9b4a4 100%)"></div>
    <h2 class="feature-title">Numquam Eius Modi Tempora</h2>
    <p class="feature-text">But I must explain to you how all this mistaken idea of denouncing pleasure and praising pain was born and I will give you a complete account of the system, and expound the actual teachings of the great explorer of the truth, the master-builder of human happi-ness. No one rejects, dislikes, or avoids pleasure itself, because it is pleasure, but because those who do not know how to pursue pleasure.</p>
    <a class="read-more" href="#" style="top:167px">Read More &gt;</a>
  </article>

  <hr class="divider" style="top:522px">

  <h2 class="gallery-title">Our Gallery</h2>
  <div class="gallery-arrows">
    <svg width="6" height="10" viewBox="0 0 6 10" aria-label="Previous"><polyline points="5,1 1,5 5,9" fill="none" stroke="#666" stroke-width="1.2"/></svg>
    <svg width="6" height="10" viewBox="0 0 6 10" aria-label="Next"><polyline points="1,1 5,5 1,9" fill="none" stroke="#666" stroke-width="1.2"/></svg>
  </div>

  <div class="gallery-grid">
    <div class="tile tile-large" role="img" aria-label="Hillside trees at sunrise"></div>
    <div class="tile" role="img" aria-label="Dirt road under blue sky" style="left:185px;top:0;width:86px;height:64px;background:linear-gradient(180deg,#5a9ad6,#c9b89a 55%,#8a7a62)"></div>
    <div class="tile" role="img" aria-label="Autumn garden path" style="left:273px;top:0;width:86px;height:64px;background:linear-gradient(180deg,#e3b62e,#6f9a3a 60%,#3f5a2a)"></div>
    <div class="tile" role="img" aria-label="Green sprouts in sunlight" style="left:362px;top:0;width:86px;height:64px;background:linear-gradient(180deg,#d6a040,#5f8f2a 55%,#3a6a1e)"></div>
    <div class="tile" role="img" aria-label="Cracked dry earth under clouds" style="left:450px;top:0;width:86px;height:64px;background:linear-gradient(180deg,#3f78c8,#d9d4cc 45%,#a48c70)"></div>
    <div class="tile" role="img" aria-label="Misty golden landscape" style="left:539px;top:0;width:86px;height:64px;background:linear-gradient(180deg,#e0a23a,#9a7236 60%,#3e3a2a)"></div>
    <div class="tile" role="img" aria-label="Green lawn with flowers" style="left:627px;top:0;width:85px;height:64px;background:linear-gradient(180deg,#c7a04a,#7ab83a 50%,#b8496a)"></div>
    <div class="tile" role="img" aria-label="Flower beds and green lawn" style="left:185px;top:68px;width:86px;height:64px;background:linear-gradient(180deg,#c83a3a,#4fb83a 45%,#2fa030)"></div>
    <div class="tile" role="img" aria-label="Hay bale on harvested field" style="left:273px;top:68px;width:86px;height:64px;background:linear-gradient(180deg,#9ec2e4,#d6a04a 50%,#9a6a2a)"></div>
    <div class="tile" role="img" aria-label="Farmland with autumn trees" style="left:362px;top:68px;width:86px;height:64px;background:linear-gradient(180deg,#a0b8d0,#b0603a 40%,#3a4a2a)"></div>
    <div class="tile" role="img" aria-label="Bare trees in winter field" style="left:450px;top:68px;width:86px;height:64px;background:linear-gradient(180deg,#9aaad8,#c0a8c0 55%,#8a7aa0)"></div>
    <div class="tile" role="img" aria-label="Lone tree under colourful night sky" style="left:539px;top:68px;width:86px;height:64px;background:linear-gradient(180deg,#1a9aa0,#5a3a8a 55%,#e03a8a)"></div>
    <div class="tile" role="img" aria-label="Purple flower meadow at dusk" style="left:627px;top:68px;width:85px;height:64px;background:linear-gradient(180deg,#6a70b8,#c07aa8 45%,#5a2a6a)"></div>
  </div>
</main>

<footer class="card site-footer">
  <div class="social" aria-label="Social links">
    <span style="background:#3b5998"></span>
    <span style="background:#2aa9e0"></span>
    <span style="background:#d64a36"></span>
  </div>
  <p class="copyright">© 2017 plotVista.&nbsp; All right reserved. Term of Use.</p>
</footer>

</body>
</html>
```